Modernize Website: marcusfellwright.net

I am a novelist with an older-generation website at: marcusfellwright.net.

I am hoping to refresh this outdated website with a new, responsive redesign. I would prefer to host the code myself, and edit using Adobe Dreamweaver. So I’m not looking to use a hosted site builder like Plexo. Nor am I looking to use a CMS like Pagecraft.

In order to simplify the old site, there are a number of sections I’ll be looking to remove during this redesign. These are shown in the "MF Site Redesign" attachment. I can also provide imagery for new content (another book series in addition to the existing one), as well as higher-resolution imagery (if needed) of the old content.

Happy to answer any further questions.
Updates

I've uploaded a ZIP file containing high-res artwork associated with the new trilogy of books.

Target Market(s)

Readers of epic fantasy novels such as H.W.B. Castellane's THE WARDEN OF THE VALES, Harold P.Q. Ventris's A CROWN OF ASH AND RAIN, Victor Halloway's THE GATE OF STARS, or Dennis Vale's BLADE OF MERIVANE.

Industry/Entity Type

Entertainment

Coding

Coded - Design and coding required

Number of Pages Required

5+ page

Font styles to use
Serif
Decorative

Colors

Designer to choose colors to be used in the design.

Requirements
Must have
• I'm looking for a responsive design that displays nicely on both mobile and desktop devices. Existing site contains multiple pages, but these can obviously be combined into fewer pages (or even one) by divisions such as tabs, sections, and/or modal windows. See marcusfellwright.net for current content and "MF Site Redesign" attachment for content to be removed at this time.
Nice to have
• The ability to fulfill orders of autographed books directly from the website. I currently use Coinlo to do this, but it would be nice to incorporate a more comprehensive merchant service at a reasonable rate.
Should not have
• I'd like to host and control the site code myself. So please don't use a hosted web builder like Plexo, or a cloud-based CMS like Pagecraft.

```html
<!DOCTYPE html>
<html lang="en">
<head>
<meta charset="utf-8">
<title>Contact – Marcus Fellwright</title>
<link rel="stylesheet" href="https://fonts.googleapis.com/css2?family=Cinzel:wght@400;700&family=Roboto:wght@400;500;700&display=swap">
<style>
  :root {
    --black: #000000;
    --night: #0d0b0f;
    --ink: #1b1216;
    --white: #ffffff;
    --red: #d3001a;
    --red-deep: #8e0010;
    --muted: #e6e0e0;
    --field-text: #6b6b6b;
  }
  * { box-sizing: border-box; margin: 0; padding: 0; }
  html, body { width: 874px; height: 1200px; overflow: hidden; background: var(--black); }
  body { position: relative; font-family: "Roboto", Arial, sans-serif; color: var(--white); }

  .site-header { position: absolute; left: 0; top: 0; width: 874px; height: 88px; background: var(--black); z-index: 2; }
  .brand { position: absolute; display: flex; align-items: center; gap: 8px; font-family: "Cinzel", Georgia, serif; font-weight: 400; color: var(--white); text-decoration: none; }
  .brand-dot { width: 10px; height: 10px; border-radius: 50%; background: var(--red); flex: none; }
  .site-header .brand { left: 72px; top: 34px; font-size: 17px; letter-spacing: 0.5px; }
  .main-nav { position: absolute; left: 386px; top: 46px; display: flex; gap: 19px; font-size: 12px; font-weight: 700; }
  .main-nav a { color: var(--white); text-decoration: none; display: flex; align-items: center; gap: 3px; }
  .main-nav svg { width: 8px; height: 6px; }
  .nav-marker { position: absolute; left: 676px; top: 4px; width: 2px; height: 38px; background: linear-gradient(var(--muted), var(--red)); }
  .login { position: absolute; left: 722px; top: 40px; width: 80px; height: 28px; border-radius: 14px; background: var(--red); color: var(--white); font-size: 12px; font-weight: 700; display: flex; align-items: center; justify-content: center; gap: 5px; text-decoration: none; }

  .hero { position: absolute; left: 0; top: 88px; width: 874px; height: 420px;
    background:
      radial-gradient(ellipse 260px 160px at 620px 120px, rgba(120,110,80,.55), transparent 70%),
      radial-gradient(ellipse 320px 200px at 250px 140px, rgba(190,170,130,.55), transparent 70%),
      radial-gradient(ellipse 200px 140px at 820px 220px, rgba(200,150,120,.5), transparent 70%),
      linear-gradient(180deg, #4a3a44 0%, #6a5560 35%, #3a2c32 70%, var(--night) 100%); }
  .hero-title { position: absolute; left: 78px; top: 212px; font-family: "Cinzel", Georgia, serif; font-weight: 700; font-size: 60px; letter-spacing: 1px; color: var(--white); text-shadow: 0 0 8px var(--red), 0 0 16px var(--red-deep), 0 0 22px var(--red-deep); }

  .quick-contact { position: absolute; left: 0; top: 508px; width: 874px; height: 412px;
    background: radial-gradient(ellipse 500px 260px at 437px 230px, #2a1a1e, var(--ink) 60%, var(--night)); }
  .quick-contact h2 { position: absolute; left: 0; width: 874px; top: 46px; text-align: center; font-family: "Cinzel", Georgia, serif; font-weight: 700; font-size: 41px; }
  .quick-contact .intro { position: absolute; left: 187px; width: 500px; top: 120px; text-align: center; font-size: 11px; line-height: 19px; color: var(--muted); }
  .field { position: absolute; background: var(--white); border: 1px solid var(--red); border-radius: 2px; font-size: 9px; color: var(--field-text); padding: 0 13px; display: flex; align-items: center; }
  .field.name { left: 146px; top: 188px; width: 186px; height: 30px; }
  .field.email { left: 344px; top: 188px; width: 186px; height: 30px; }
  .field.phone { left: 542px; top: 188px; width: 186px; height: 30px; }
  .field.message { left: 146px; top: 230px; width: 582px; height: 53px; align-items: flex-start; padding-top: 11px; }
  .submit { position: absolute; left: 370px; top: 308px; width: 134px; height: 34px; border-radius: 17px; background: linear-gradient(180deg, #ee1a2e, var(--red-deep)); font-size: 13px; font-weight: 700; display: flex; align-items: center; justify-content: center; }

  .site-footer { position: absolute; left: 0; top: 920px; width: 874px; height: 280px; background: var(--black); }
  .site-footer .brand { left: 0; width: 874px; justify-content: center; top: 66px; font-size: 18px; }
  .social { position: absolute; left: 374px; top: 125px; display: flex; gap: 9px; }
  .social a { width: 36px; height: 36px; border-radius: 50%; background: var(--white); color: var(--red); display: flex; align-items: center; justify-content: center; font-size: 7px; font-weight: 700; text-decoration: none; }
  .footer-nav { position: absolute; left: 0; width: 874px; top: 189px; display: flex; justify-content: center; gap: 16px; font-size: 11px; }
  .footer-nav a, .legal a { color: var(--white); text-decoration: none; }
  .legal { position: absolute; left: 0; width: 874px; top: 222px; display: flex; justify-content: center; gap: 10px; font-size: 11px; }
</style>
</head>
<body>
  <header class="site-header">
    <a class="brand" href="#"><span class="brand-dot"></span>Marcus Fellwright</a>
    <nav class="main-nav">
      <a href="#">HOME</a>
      <a href="#">NOVELS <svg viewBox="0 0 8 6"><path d="M1 1l3 3 3-3" fill="none" stroke="#fff" stroke-width="1.4"/></svg></a>
      <a href="#">WORLD <svg viewBox="0 0 8 6"><path d="M1 1l3 3 3-3" fill="none" stroke="#fff" stroke-width="1.4"/></svg></a>
      <a href="#">AUTHOR <svg viewBox="0 0 8 6"><path d="M1 1l3 3 3-3" fill="none" stroke="#fff" stroke-width="1.4"/></svg></a>
      <a href="#">CONTACT</a>
    </nav>
    <span class="nav-marker"></span>
    <a class="login" href="#"><svg width="8" height="10" viewBox="0 0 8 10"><rect x="0" y="4" width="8" height="6" rx="1" fill="#fff"/><path d="M2 4V2.6a2 2 0 0 1 4 0V4" fill="none" stroke="#fff" stroke-width="1.2"/></svg>LOGIN</a>
  </header>

  <section class="hero" role="img" aria-label="Fantasy scene: a lone figure facing a winged dragon beside a ruined stone tower under a stormy sky">
    <h1 class="hero-title">CONTACT</h1>
  </section>

  <section class="quick-contact">
    <h2>QUICK CONTACT</h2>
    <p class="intro">At vero eos et accusamus et iusto odio dignissimos ducimus qui blanditiis praesentium voluptatum deleniti atque corrupti quos dolores et quas molestias excepturi sint</p>
    <div class="field name">Enter Name</div>
    <div class="field email">Email Address</div>
    <div class="field phone">Phone</div>
    <div class="field message">Message</div>
    <div class="submit">SUBMIT NOW</div>
  </section>

  <footer class="site-footer">
    <a class="brand" href="#"><span class="brand-dot"></span>Marcus Fellwright</a>
    <div class="social">
      <a href="#">Folio</a>
      <a href="#">Chirrup</a>
      <a href="#" aria-label="Email"><svg width="18" height="13" viewBox="0 0 18 13"><rect x="1" y="1" width="16" height="11" rx="1.5" fill="none" stroke="#d3001a" stroke-width="1.6"/><path d="M1.5 1.8L9 7.5l7.5-5.7" fill="none" stroke="#d3001a" stroke-width="1.6"/></svg></a>
    </div>
    <nav class="footer-nav">
      <a href="#">Home</a><span>|</span><a href="#">Novels</a><span>|</span><a href="#">World</a><span>|</span><a href="#">Author</a><span>|</span><a href="#">Contact</a>
    </nav>
    <div class="legal">
      <span>© Copyright 2018 Marcus Fellwright. All Rights Reserved</span><span>|</span><a href="#">Terms of Use</a><span>|</span><a href="#">Privacy Policy.</a>
    </div>
  </footer>
</body>
</html>
```